Brightway Haus Inc. Business Card Design

Brightway Haus Inc. is in search of a great clean design for our business cards!

Looking to incorporate our full logo and watermark on side one (however, I am open to having the text and watermark separated within the design.)

On side two, I am looking to have contact information (Name, Position, Phone #, Email, Website (www.thebrightwayhaus.ca). Can have the logo and/or watermark as part of the design if applicable.

Please add tagline "Where Shine Counts" on either side 1 or 2. This tagline can be in a sans serif, serif or cursive font as long as it compliments overall design. Capitalization can be title or sentence case depending on how it fits within the design.

Get creative!! Looking for a clean, crisp, premium design! Looking for a glossy card finish with spot UV features when printed. Cards will also be printed with rounded corners. Standard dimensions (3.5 x 2).

Target Market(s)

B2B - primary clients are business owners or property management corporations. (residential jobs are few and far between)

Industry/Entity Type

Business

Contact Information for Business Card

- clean, crisp design
- double sided
- spot UV accents and glossy finish upon printing
- standard business card size (3.5 x 2) with rounded corners
- please see project description for requirements per side

Font styles to use
Sans Serif

Requirements
Must have
• - adequate bleeds with print ready files
• - cohesive design elements between side 1 & 2
• - spot UV elements (can be on both sides or just one, use your discretion)
• - colour pallet should match the logo file provided
• - incorporate tagline "where shine counts" (this tagline can be in a serif or sans serif font as long as it is complimentary to the overall design.
Nice to have
• - Premium elements with a clean design
Should not have
• - Please omit cartoon or whimsical like designs, think premium.
• - Colours should not stray from the pallet of the provided logo.

```html
<!DOCTYPE html>
<html lang="en">
<head>
<meta charset="utf-8">
<title>Brightway Haus Inc. Business Card</title>
<link href="https://fonts.googleapis.com/css2?family=Roboto:wght@400;500;700&display=swap" rel="stylesheet">
<style>
  :root {
    --page: #d8d8d8;
    --card-light: #f2f2f2;
    --card-mid: #e6e6e6;
    --teal: #12a09a;
    --navy: #1f2147;
    --ink: #23254a;
    --watermark: rgba(255, 255, 255, 0.55);
  }
  * { margin: 0; padding: 0; box-sizing: border-box; }
  html, body {
    width: 1200px; height: 576px; overflow: hidden;
    background: var(--page);
    font-family: "Roboto", Arial, sans-serif;
  }
  .canvas { position: relative; width: 1200px; height: 576px; }
  .card {
    position: absolute; top: 139px;
    width: 484px; height: 292px;
    border-radius: 12px;
    background: linear-gradient(160deg, var(--card-light) 0%, var(--card-mid) 100%);
    box-shadow: 0 2px 6px rgba(0,0,0,0.18);
    overflow: hidden;
  }
  .card--front { left: 82px; }
  .card--back { left: 602px; width: 482px; }
  .watermark {
    position: absolute; right: 20px; top: 0;
    width: 230px; height: 292px;
    background: radial-gradient(ellipse at 55% 55%, var(--watermark) 0%, rgba(255,255,255,0) 70%);
  }
  .brand {
    position: absolute; display: flex; align-items: center;
    color: var(--teal); font-weight: 700; white-space: nowrap;
  }
  .brand__mark { background: var(--navy); flex: none; }
  .card--front .brand { left: 56px; top: 128px; font-size: 31px; gap: 10px; }
  .card--front .brand__mark { width: 34px; height: 34px; }
  .back-brand {
    position: absolute; left: 30px; top: 86px; width: 212px;
    display: flex; flex-direction: column; align-items: center;
  }
  .back-brand__mark { width: 52px; height: 52px; background: var(--navy); }
  .back-brand__name {
    margin-top: 16px; color: var(--teal); font-weight: 700; font-size: 17.5px;
    white-space: nowrap;
  }
  .tagline {
    margin-top: 4px; color: var(--navy); font-size: 11.5px;
    letter-spacing: 2.6px; white-space: nowrap;
  }
  .contact { position: absolute; left: 282px; top: 68px; color: var(--ink); }
  .contact__name { color: var(--teal); font-weight: 700; font-size: 21px; line-height: 24px; }
  .contact__role { font-size: 12px; margin-top: 2px; }
  .contact__address { font-size: 12.5px; line-height: 16px; margin-top: 26px; }
  .contact__list { list-style: none; margin-top: 3px; }
  .contact__item {
    display: flex; align-items: center; gap: 8px;
    font-size: 13px; line-height: 18px;
  }
  .contact__icon { width: 11px; height: 11px; fill: var(--teal); flex: none; }
  .accent { color: var(--teal); }
</style>
</head>
<body>
<main class="canvas">
  <section class="card card--front">
    <div class="watermark" role="img" aria-label="Faint spot UV brand watermark"></div>
    <div class="brand">
      <span class="brand__mark"></span>
      <span class="brand__name">BRIGHTWAY HAUS INC.</span>
    </div>
  </section>

  <section class="card card--back">
    <div class="watermark" role="img" aria-label="Faint spot UV brand watermark"></div>
    <div class="back-brand">
      <span class="back-brand__mark"></span>
      <span class="back-brand__name">BRIGHTWAY HAUS INC.</span>
      <span class="tagline">Where Shine Counts</span>
    </div>
    <div class="contact">
      <p class="contact__name">Daniel Reyes</p>
      <p class="contact__role">Managing Director</p>
      <p class="contact__address">48 Harbour Line Road<br>Unit 7, Canada 204</p>
      <ul class="contact__list">
        <li class="contact__item">
          <svg class="contact__icon" viewBox="0 0 12 12"><path d="M1 4c0-2 2-3 5-3s5 1 5 3l-2 1-1-2H4L3 5 1 4zm2 2h6l1 5H2l1-5zm3 1a1.5 1.5 0 1 0 0 3 1.5 1.5 0 0 0 0-3z"/></svg>
          <span>1800-555-0148</span>
        </li>
        <li class="contact__item">
          <svg class="contact__icon" viewBox="0 0 12 12"><path d="M0 2h12v1L6 7 0 3zm0 2.5 6 4 6-4V10H0z"/></svg>
          <span>dreyes@brightwayhaus.ca</span>
        </li>
        <li class="contact__item">
          <svg class="contact__icon" viewBox="0 0 12 12"><path d="M6 0a6 6 0 1 0 0 12A6 6 0 0 0 6 0zm0 1c.8 0 1.6 1.4 1.9 4H4.1C4.4 2.4 5.2 1 6 1zM1 6.5h2.1c0 1.4.3 2.6.7 3.5A5 5 0 0 1 1 6.5zm0-1A5 5 0 0 1 3.8 2c-.4.9-.7 2.1-.7 3.5zm5 5.5c-.8 0-1.6-1.4-1.9-4.5h3.8C7.6 9.6 6.8 11 6 11zm2.2-1c.4-.9.7-2.1.7-3.5H11A5 5 0 0 1 8.2 10zM8.9 5.5c0-1.4-.3-2.6-.7-3.5A5 5 0 0 1 11 5.5z"/></svg>
          <span>www.<span class="accent">thebrightwayhaus</span>.ca</span>
        </li>
      </ul>
    </div>
  </section>
</main>
</body>
</html>
```